6 page (for now) squarespace website design for a Mobile Fitness small business

My sons California based small business "BrenVale Coaching" with new subsidiary called "BrenVale 4 Kids". I don't understand coding the website, is that the function squarespace provides?
In the end I want a working website, squarespace, I have a google workspace domain, email and subscription to squarespace & google workspace. URLs include brenvalecoaching.example and brenvale4kids.example. I have an idea of what I am looking for in a website and I have some examples of website designs I like, but I am 100% open to your design concepts and artistic flair. email is torin@brenvalecoaching.example
I am looking for someone to design the site, help me understand how to make "minor" changes and hopefully have a long term relationship on the tech side of the business. I need an Idea of pricing for future changes (Rate T&M).
There are 2 businesses so I need a way to incorporate both the main company and a subsidiary into 1 website or link it somehow. I am open to your suggestions how to accomplish that. Do I need 2 completely separate websites or can it be done on 1 site directing you to different pages. I read conflicting info if it is a BAD idea to link 2 different websites so I will defer to your advice.
Below are the pages I need designed:
- Home Page- BrenVale Coaching
- Home Page- BrenVale 4 Kids (Homeschool market)
- Member Page (subscription service?)
- Workouts- with video clips 1-6 min each
- About
- Contact
- FAQ's
Future work & page designs:
- Store with training subscriptions & a few merch items
- Booking Appointments
- Bookshelf
- email campaign
-Blog
I like the feel of this website:
https://zestlope.example/

```html
<!DOCTYPE html>
<html lang="en">
<head>
<meta charset="utf-8">
<title>BrenVale Coaching</title>
<link href="https://fonts.googleapis.com/css2?family=Poppins:ital,wght@0,400;0,500;0,600;0,700;1,400&family=Lato:wght@400&display=swap" rel="stylesheet">
<style>
:root{
  --ink:#222;
  --text:#444;
  --muted:#555;
  --white:#fff;
  --dark-btn:#333;
  --black:#111;
  --gray-band:#f1f1f1;
  --hero-a:#2a2d33;
  --hero-b:#5a1f22;
  --hero-c:#1c1e22;
}
*{box-sizing:border-box;margin:0;padding:0}
html,body{width:1200px;height:2960px;overflow:hidden}
body{font-family:"Poppins",sans-serif;color:var(--ink);background:var(--white);position:relative}
a{color:inherit;text-decoration:none}

.site-header{position:absolute;top:0;left:0;width:1200px;height:129px;background:var(--white)}
.brand{position:absolute;left:76px;top:22px;width:140px;text-align:center}
.brand-mark{display:block;width:34px;height:34px;margin:0 auto 10px;background:var(--black)}
.brand-name{font-size:22px;letter-spacing:5px;font-weight:500;color:var(--black)}
.main-nav{position:absolute;left:255px;top:52px;display:flex;gap:30px;font-size:16px;font-weight:500}
.btn-book{position:absolute;left:924px;top:36px;width:201px;height:54px;background:var(--dark-btn);color:var(--white);font-size:18px;display:flex;align-items:center;justify-content:center}

.hero{position:absolute;top:129px;left:0;width:1200px;height:576px;
  background:linear-gradient(100deg,var(--hero-b) 0%,var(--hero-a) 35%,#3b3f46 60%,var(--hero-c) 100%);
  text-align:center;color:var(--white)}
.hero h1{position:absolute;top:172px;width:100%;font-size:62px;font-weight:700;line-height:1}
.hero p{position:absolute;top:243px;left:200px;width:800px;font-size:25px;font-weight:500;line-height:40px}
.hero .btn-hero{position:absolute;left:500px;top:337px;width:200px;height:54px;background:var(--black);font-size:18px;display:flex;align-items:center;justify-content:center}

.card{position:absolute;width:512px;height:427px;color:var(--white);text-align:center;display:flex;flex-direction:column;justify-content:center}
.card h2{font-size:32px;font-weight:600;line-height:1.2}
.card span{font-size:19px;font-style:italic;margin-top:10px}
.card-coaching{left:75px;top:764px;background:linear-gradient(135deg,#6a5a4c,#3a302a)}
.card-kids{left:615px;top:764px;background:linear-gradient(135deg,#5c6168,#7a4a2c 55%,#4d5157)}
.card-workouts{left:75px;top:1219px;background:linear-gradient(135deg,#6e655c,#4b4f58 60%,#8a8c90)}
.card-store{left:615px;top:1219px;background:linear-gradient(135deg,#6a6a6a,#3f3f42)}

.about{position:absolute;top:1726px;left:0;width:1200px;height:489px;background:var(--gray-band);text-align:center}
.about h2{position:absolute;top:100px;width:100%;font-size:32px;font-weight:400;color:var(--text)}
.about p{position:absolute;top:162px;left:150px;width:900px;font-size:17px;line-height:33px;color:var(--muted)}
.btn-outline{position:absolute;left:510px;top:329px;width:180px;height:54px;border:1px solid #999;font-size:17px;color:var(--text);display:flex;align-items:center;justify-content:center}

.membership{position:absolute;top:2215px;left:0;width:1200px;height:431px;
  background:radial-gradient(ellipse at 30% 50%,#4a4d55,#1e2026 75%);text-align:center;color:var(--white)}
.membership h2{position:absolute;top:100px;width:100%;font-size:42px;font-weight:400}
.membership p{position:absolute;top:170px;left:160px;width:880px;font-size:17px;line-height:33px}
.membership .btn-outline{top:266px;border-color:#ccc;color:var(--white)}

.site-footer{position:absolute;top:2646px;left:0;width:1200px;height:314px}
.site-footer .brand{left:75px;top:50px}
.copyright{position:absolute;left:68px;top:175px;font-family:"Lato",sans-serif;font-size:15px;line-height:26px;color:var(--muted)}
.social{position:absolute;left:68px;top:244px;display:flex;gap:22px}
.social span{display:block;width:22px;height:22px;border-radius:50%;background:var(--text)}
.foot-col{position:absolute;top:64px;list-style:none;font-size:15px;font-weight:500;line-height:33px}
.foot-col-1{left:385px}
.foot-col-2{left:625px}
.btn-contact{position:absolute;left:946px;top:67px;width:180px;height:54px;background:var(--dark-btn);color:var(--white);font-size:18px;display:flex;align-items:center;justify-content:center}
</style>
</head>
<body>

<header class="site-header">
  <a class="brand" href="#"><span class="brand-mark"></span><span class="brand-name">BRENVALE</span></a>
  <nav class="main-nav">
    <a href="#">BrenVale Coaching</a>
    <a href="#">BrenVale 4 Kids</a>
    <a href="#">Workouts</a>
    <a href="#">About</a>
    <a href="#">Contact</a>
    <a href="#">FAQ's</a>
  </nav>
  <a class="btn-book" href="#">Book Appointment</a>
</header>

<section class="hero" role="img" aria-label="Athletes training with battle ropes in a gym">
  <h1>Welcome to BrenVale</h1>
  <p>Nemo enim ipsam voluptatem quia voluptas sit aspernatur aut odit aut fugit.</p>
  <a class="btn-hero" href="#">Book Appointment</a>
</section>

<a class="card card-coaching" href="#" role="img" aria-label="Coach guiding a woman lifting dumbbells"><h2>BrenVale Coaching</h2><span>Learn More</span></a>
<a class="card card-kids" href="#" role="img" aria-label="Children doing exercises on step platforms"><h2>BrenVale 4 Kids</h2><span>Learn More</span></a>
<a class="card card-workouts" href="#" role="img" aria-label="People running on treadmills"><h2>Workouts</h2><span>Learn More</span></a>
<a class="card card-store" href="#" role="img" aria-label="Woman resting on a mat with training gear"><h2>Store with Training</h2><span>Learn More</span></a>

<section class="about">
  <h2>About BrenVale</h2>
  <p>Sed ut perspiciatis unde omnis iste natus error sit voluptatem accusantium doloremque laudantium, totam rem aperiam, eaque ipsa quae ab illo inventore veritatis et quasi architecto beatae vitae dicta sunt explicabo. Nemo enim ipsam voluptatem quia voluptas sit aspernatur aut odit aut fugit, sed quia consequuntur magni dolores eos qui ratione voluptatem.</p>
  <a class="btn-outline" href="#">Read More</a>
</section>

<section class="membership" role="img" aria-label="Dumbbells on a rack, darkened background">
  <h2>Membership Subscription</h2>
  <p>Sed ut perspiciatis unde omnis iste natus error sit voluptatem accusantium doloremque laudantium, totam rem aperiam, eaque ipsa quae ab illo inventore veritatis .</p>
  <a class="btn-outline" href="#">Subscribe Now</a>
</section>

<footer class="site-footer">
  <a class="brand" href="#"><span class="brand-mark"></span><span class="brand-name">BRENVALE</span></a>
  <p class="copyright">Copyright © 2022 CompanyName<br>All Right Reserved</p>
  <div class="social">
    <span aria-label="Social link"></span><span aria-label="Social link"></span><span aria-label="Social link"></span><span aria-label="Social link"></span><span aria-label="Social link"></span>
  </div>
  <ul class="foot-col foot-col-1">
    <li>BrenVale Coaching</li><li>BrenVale 4 Kids</li><li>Workouts</li><li>About</li><li>Contact</li><li>FAQ's</li>
  </ul>
  <ul class="foot-col foot-col-2">
    <li>Store with training subscriptions</li><li>Booking Appointments</li><li>Bookshelf</li><li>Email campaign</li><li>Blog</li>
  </ul>
  <a class="btn-contact" href="#">Contact Us</a>
</footer>

</body>
</html>
```